English and Spanish Language School Needs a Business Card

Need a business card design a startup company called Maribel Language School. The company will offer English and Spanish conversational level courses designed to make the learner feel comfortable with grammar and vocabulary. We would like to see a logo with some colour that should communicate learning, growth.

Target Market(s)

Consumers and businesses

Industry/Entity Type

Education

Contact Information for Business Card

TBD

Font styles to use
Serif

Requirements
Must have
• Include the following
• Logo
• Name
• Title
• Cellphone Number
• Office Phone number
• Email address
• Office Address

```html
<!DOCTYPE html>
<html lang="en">
<head>
<meta charset="utf-8">
<title>Maribel Language School – Business Card</title>
<link rel="stylesheet" href="https://fonts.googleapis.com/css2?family=Source+Sans+3:wght@400;600;700&display=swap">
<style>
  :root {
    --stage: #1c1c1c;
    --brand-red: #c41f26;
    --brand-red-light: #cf2a30;
    --card-white: #ffffff;
    --ink: #333333;
  }
  html, body {
    margin: 0;
    padding: 0;
    width: 1200px;
    height: 900px;
    overflow: hidden;
    background: var(--stage);
    font-family: "Source Sans 3", "Myriad Pro", Arial, sans-serif;
  }
  .stage {
    position: relative;
    width: 1200px;
    height: 900px;
  }
  .card {
    position: absolute;
    top: 170px;
    width: 347px;
    height: 561px;
    overflow: hidden;
  }
  .card-front { left: 259px; background: var(--card-white); }
  .card-back { left: 631px; background: var(--brand-red); }

  .accent-tab {
    position: absolute;
    left: 102px;
    width: 143px;
    background: var(--brand-red);
  }
  .accent-tab-top { top: 0; height: 30px; }
  .accent-tab-bottom { bottom: 0; height: 28px; }

  .wordmark {
    position: absolute;
    left: 0;
    right: 0;
    text-align: center;
    font-weight: 700;
    line-height: 1;
    margin: 0;
  }
  .wordmark .wordmark-name { display: block; font-size: 58px; letter-spacing: -1px; }
  .wordmark .wordmark-tagline { display: block; font-size: 20px; margin-top: 4px; }

  .card-front .wordmark { top: 128px; color: var(--brand-red); }
  .card-back .wordmark { top: 228px; color: var(--card-white); }

  .contact {
    position: absolute;
    left: 0;
    right: 0;
    top: 308px;
    text-align: center;
    color: var(--ink);
    font-size: 15px;
    line-height: 21px;
  }
  .contact p { margin: 0; }
  .contact .person-name {
    color: var(--brand-red);
    font-size: 21px;
    font-weight: 600;
    line-height: 26px;
    margin-bottom: 1px;
  }
  .contact .person-title { margin-bottom: 24px; }
  .contact .phones { margin-bottom: 18px; }
  .contact .address { line-height: 17px; }

  .backdrop-mark {
    position: absolute;
    left: -60px;
    top: 250px;
    width: 520px;
    transform: rotate(-68deg);
    transform-origin: center;
    color: var(--brand-red-light);
    font-weight: 700;
    line-height: 1;
    white-space: nowrap;
    text-align: center;
  }
  .backdrop-mark .wordmark-name { display: block; font-size: 150px; }
  .backdrop-mark .wordmark-tagline { display: block; font-size: 40px; }
</style>
</head>
<body>
<main class="stage">
  <section class="card card-front" aria-label="Business card front">
    <div class="accent-tab accent-tab-top"></div>
    <h1 class="wordmark">
      <span class="wordmark-name">Maribel</span>
      <span class="wordmark-tagline">Language School</span>
    </h1>
    <div class="contact">
      <p class="person-name">DANIEL REYES</p>
      <p class="person-title">Managing Director</p>
      <div class="phones">
        <p>555-210-4836</p>
        <p>555-210-4837</p>
        <p>hello@maribelschool.com</p>
      </div>
      <div class="address">
        <p>48, Alder Street</p>
        <p>Westford, 204518</p>
      </div>
    </div>
    <div class="accent-tab accent-tab-bottom"></div>
  </section>

  <section class="card card-back" aria-label="Business card back">
    <div class="backdrop-mark" aria-hidden="true">
      <span class="wordmark-name">Maribel</span>
      <span class="wordmark-tagline">Language School</span>
    </div>
    <p class="wordmark">
      <span class="wordmark-name">Maribel</span>
      <span class="wordmark-tagline">Language School</span>
    </p>
  </section>
</main>
</body>
</html>
```